Web design project for exciting Australian start-up

Background
We are looking for a creative and talented web design artist to work alongside our market leading web developer.
• You will be required to create a modern and clean design theme for our website, incorporating selected rustic colour scheme elements for our exciting Australian start-up to operate within the coffee industry.
reoccurring work to be expected to flow to the successful designer.
Requirements
• c. 5 - 10 page website
• Landing page
• Log in/ out
• 404 template
• Typography is emphasised
• Please use either a) typemarrow.com, b) free web fonts, c) brindle fonts
• All design elements in vector format
• Preferably with icons for each header title(i.e. about us, how it works etc) but designer have free reign over how the site looks, so might not be applicable
• All pages to be responsive
• Down to eSlab resolution

High level visual design brief attached - additional pages to be worked from base design.

Design inspiration
• We would like to use design elements from the following sources:
http://www.zandrix.com/halcyon/ (Functionality)
Colour scheme refer to logo and complementary style guide

```html
<!DOCTYPE html>
<html lang="en">
<head>
<meta charset="utf-8">
<title>Brewline Hub</title>
<link rel="stylesheet" href="https://fonts.googleapis.com/css2?family=Open+Sans:wght@300;400;700;800&display=swap">
<style>
  :root {
    --orange: #ff8200;
    --charcoal: #3a3a3a;
    --ink: #222222;
    --white: #ffffff;
    --black: #000000;
    --logo-ink: #2b2b2b;
    --net-blue: #3b5998;
    --net-cyan: #2fb4e0;
    --net-navy: #0a66c2;
    --net-red: #e52d27;
  }
  * { margin: 0; padding: 0; box-sizing: border-box; }
  html, body { width: 1200px; height: 875px; overflow: hidden; background: var(--white); }
  body { position: relative; font-family: "Open Sans", Arial, sans-serif; }

  .site-header { position: absolute; left: 0; top: 0; width: 1200px; height: 108px; background: var(--white); }
  .brand { position: absolute; left: 157px; top: 30px; display: flex; align-items: center; gap: 10px; }
  .brand-mark { width: 40px; height: 40px; border-radius: 50%; background: var(--orange); }
  .brand-name { font-weight: 800; font-size: 27px; letter-spacing: 1px; color: var(--logo-ink); text-transform: uppercase; }
  .account-actions { position: absolute; left: 869px; top: 33px; display: flex; height: 36px; }
  .account-actions a { display: flex; align-items: center; justify-content: center; height: 100%; font-weight: 700; font-size: 13.5px; color: var(--white); text-decoration: none; }
  .btn-login { width: 83px; background: var(--orange); border-radius: 3px 0 0 3px; }
  .btn-signup { width: 83px; background: var(--charcoal); border-radius: 0 3px 3px 0; }
  .header-rule { position: absolute; left: 0; top: 108px; width: 1200px; height: 8px; background: var(--orange); }

  .hero { position: absolute; left: 0; top: 116px; width: 1200px; height: 482px; overflow: hidden; }
  .hero-photo { position: absolute; inset: 0;
    background:
      radial-gradient(ellipse 260px 230px at 800px 250px, #e9e6e2 0%, #cfc9c2 55%, rgba(120,80,50,0) 100%),
      radial-gradient(ellipse 240px 160px at 90px 40px, #a08460 0%, rgba(100,70,40,0) 100%),
      linear-gradient(100deg, #5a3a24 0%, #3a2416 45%, #2a170c 75%, #3a2214 100%); }
  .hero-card { position: absolute; left: 164px; top: 64px; width: 296px; height: 329px; background: var(--orange); }
  .hero-title { position: absolute; left: 17px; top: 24px; font-weight: 300; font-size: 46px; line-height: 41px; color: var(--white); }
  .btn-video { position: absolute; left: 35px; top: 246px; width: 225px; height: 52px; background: var(--ink); display: flex; align-items: center; gap: 12px; padding-left: 20px; color: var(--white); font-weight: 400; font-size: 23px; text-decoration: none; }
  .slider-arrow { position: absolute; top: 213px; width: 40px; height: 64px; }
  .slider-prev { left: 118px; }
  .slider-next { left: 1042px; }

  .site-footer { position: absolute; left: 0; top: 598px; width: 1200px; height: 277px; background: var(--black); color: var(--white); }
  .footer-col { position: absolute; top: 36px; }
  .footer-col h2 { font-size: 13px; font-weight: 700; margin-bottom: 21px; }
  .footer-col ul { list-style: none; }
  .footer-col li { font-size: 13px; line-height: 20.5px; }
  .col-help { left: 166px; }
  .col-about { left: 538px; }
  .col-social { left: 906px; }
  .col-social li { display: flex; justify-content: space-between; align-items: center; width: 129px; line-height: 22px; }
  .social-dot { width: 19px; height: 19px; border-radius: 50%; }
  .dot-blue { background: var(--net-blue); }
  .dot-cyan { background: var(--net-cyan); }
  .dot-navy { background: var(--net-navy); }
  .dot-red { background: var(--net-red); }
  .copyright { position: absolute; left: 0; top: 193px; width: 1200px; text-align: center; font-size: 13px; }
</style>
</head>
<body>
  <header class="site-header">
    <div class="brand">
      <span class="brand-mark"></span>
      <span class="brand-name">Brewline Hub</span>
    </div>
    <nav class="account-actions">
      <a class="btn-login" href="#">LOGIN</a>
      <a class="btn-signup" href="#">SIGN UP</a>
    </nav>
  </header>
  <div class="header-rule"></div>

  <section class="hero">
    <div class="hero-photo" role="img" aria-label="Cup of coffee on a saucer with cinnamon sticks and star anise, surrounded by roasted coffee beans and a burlap sack on a wooden table"></div>
    <svg class="slider-arrow slider-prev" viewBox="0 0 40 64" aria-label="Previous slide"><polyline points="32,4 8,32 32,60" fill="none" stroke="#fff" stroke-width="8"/></svg>
    <svg class="slider-arrow slider-next" viewBox="0 0 40 64" aria-label="Next slide"><polyline points="8,4 32,32 8,60" fill="none" stroke="#fff" stroke-width="8"/></svg>
    <div class="hero-card">
      <h1 class="hero-title">Australia’s<br>first online<br>coffee<br>marketplace</h1>
      <a class="btn-video" href="#">
        <svg width="34" height="34" viewBox="0 0 34 34" aria-hidden="true"><circle cx="17" cy="17" r="17" fill="#fff"/><polygon points="13,9 26,17 13,25" fill="#222"/></svg>
        Watch Video
      </a>
    </div>
  </section>

  <footer class="site-footer">
    <div class="footer-col col-help">
      <h2>Helpful info</h2>
      <ul><li>About us</li><li>Media enquiries</li><li>Terms &amp; conditions</li><li>Privacy policy</li></ul>
    </div>
    <div class="footer-col col-about">
      <h2>Who we are Join us on</h2>
      <ul><li>How it works</li><li>FAQ</li><li>Contact us</li></ul>
    </div>
    <div class="footer-col col-social">
      <h2>Join us on</h2>
      <ul>
        <li>Circlenet <span class="social-dot dot-blue"></span></li>
        <li>Chirpwire <span class="social-dot dot-cyan"></span></li>
        <li>Workgraph <span class="social-dot dot-navy"></span></li>
        <li>Clipstream <span class="social-dot dot-red"></span></li>
      </ul>
    </div>
    <p class="copyright">Copyright © 2014 Brewline Hub</p>
  </footer>
</body>
</html>
```